Awesome photographers card for an awesome new business

Double sided business card Black background and silver logo in middle on one side. Details on otherside. please keep it simple

Industry/Entity Type

Photographer

Contact Information for Business Card

Gerald Fenwick
0452817360
GeraldFenwickPhotography47@mailbox.test
www.GeraldFenwickPhotography.test.au
Instagram _Gerald_fenwick

Requirements
Must have
• My logo in Silver
• please use instagram logo instead of "Instagram"

```html
<!DOCTYPE html>
<html lang="en">
<head>
<meta charset="utf-8">
<title>Gerald Fenwick Photography – Business Card</title>
<link rel="stylesheet" href="https://fonts.googleapis.com/css2?family=Roboto:wght@400&family=Roboto+Condensed:wght@700&display=swap">
<style>
  :root {
    --backdrop: #1b1b1c;
    --card-light: #f4f4f4;
    --card-dark: #1c1d1f;
    --band-top: #8a8a8a;
    --band-mid: #c4c4c4;
    --band-bottom: #6a6a6a;
    --ink-name: #5a5a5a;
    --ink-body: #444444;
    --silver: #b9b9b9;
    --silver-dark: #8c8c8c;
    --ink-web: #e6e6e6;
  }
  html, body {
    margin: 0;
    width: 1200px;
    height: 960px;
    overflow: hidden;
    background: var(--backdrop);
  }
  .canvas {
    position: relative;
    width: 1200px;
    height: 960px;
  }
  .card {
    position: absolute;
    width: 600px;
    height: 342px;
    box-shadow: 0 3px 8px rgba(0,0,0,0.55);
    overflow: hidden;
  }
  .card--front { left: 314px; top: 113px; background: var(--card-light); }
  .card--back  { left: 312px; top: 473px; background: var(--card-dark); height: 341px; }

  .front__band {
    position: absolute;
    left: 482px; top: 0;
    width: 118px; height: 100%;
    background: linear-gradient(160deg, var(--band-top) 0%, var(--band-mid) 38%, var(--band-bottom) 100%);
  }
  .brand-mark {
    position: absolute;
    display: flex;
    align-items: center;
    justify-content: center;
    border-radius: 50%;
    box-sizing: border-box;
    font-family: "Roboto", sans-serif;
    font-weight: 400;
    text-align: center;
    letter-spacing: 1.5px;
    line-height: 1.3;
  }
  .card--front .brand-mark {
    left: 415px; top: 44px;
    width: 136px; height: 136px;
    border: 3px solid var(--silver-dark);
    color: var(--ink-name);
    font-size: 11px;
  }
  .card--back .brand-mark {
    left: 213px; top: 77px;
    width: 170px; height: 170px;
    border: 3px solid var(--silver);
    color: var(--silver);
    font-size: 13px;
  }

  .front__name {
    position: absolute;
    left: 34px; top: 195px;
    margin: 0;
    font-family: "Roboto Condensed", sans-serif;
    font-weight: 700;
    font-size: 21px;
    color: var(--ink-name);
    letter-spacing: 0.2px;
  }
  .contact-list {
    position: absolute;
    left: 35px; top: 235px;
    margin: 0; padding: 0;
    list-style: none;
    font-family: "Roboto", sans-serif;
    font-size: 14.5px;
    color: var(--ink-body);
  }
  .contact-list li {
    display: flex;
    align-items: center;
    height: 19px;
  }
  .contact-list .icon {
    width: 14px; height: 14px;
    margin-right: 12px;
    fill: var(--ink-body);
    flex: none;
  }
  .icon--plain-square {
    width: 12px; height: 12px;
    margin: 0 14px 0 1px;
    background: var(--ink-body);
    flex: none;
  }

  .back__web {
    position: absolute;
    left: 0; right: 0; top: 290px;
    margin: 0;
    text-align: center;
    font-family: "Roboto", sans-serif;
    font-size: 15px;
    letter-spacing: 2.2px;
    color: var(--ink-web);
  }
</style>
</head>
<body>
<main class="canvas">

  <section class="card card--front" aria-label="Business card, details side">
    <div class="front__band"></div>
    <div class="brand-mark">GERALD<br>FENWICK<br>PHOTOGRAPHY</div>

    <h1 class="front__name">GERALD FENWICK</h1>
    <ul class="contact-list">
      <li>
        <svg class="icon" viewBox="0 0 16 16" aria-hidden="true"><path d="M3.6 1.2l2.3 2.4-1.3 1.8c.8 1.9 2.3 3.5 4.3 4.4l1.8-1.3 2.4 2.3-1.3 2.4C6.4 13 2.8 9.4 1.2 4.2z"/></svg>
        0452817360
      </li>
      <li>
        <svg class="icon" viewBox="0 0 16 16" aria-hidden="true"><path d="M1.5 3.5h13v9h-13z M2 4l6 4.5L14 4" fill="none" stroke="#444" stroke-width="0"/><path d="M1.5 4h13v1.2L8 9 1.5 5.2z"/><path d="M1.5 6.4L8 10.2l6.5-3.8V12.5h-13z"/></svg>
        GeraldFenwickPhotography47@mailbox.test
      </li>
      <li>
        <svg class="icon" viewBox="0 0 16 16" aria-hidden="true"><circle cx="8" cy="8" r="6.5" fill="none" stroke="#444" stroke-width="1.6"/><path d="M5 4.5l2.5 1-1 2.5 2 1.5-.5 3L5.5 10 4 6.5z M9.5 3.5l2.5 1.5-1 2-2-.5z"/></svg>
        www.GeraldFenwickPhotography.test.au
      </li>
      <li>
        <span class="icon--plain-square" aria-hidden="true"></span>
        Gerald_fenwick
      </li>
    </ul>
  </section>

  <section class="card card--back" aria-label="Business card, logo side">
    <div class="brand-mark">GERALD<br>FENWICK<br>PHOTOGRAPHY</div>
    <p class="back__web">www.GeraldFenwickPhotography.test.au</p>
  </section>

</main>
</body>
</html>
```